Company web site

Looking for a full responsive(mobile friendly) wordpress implementation

Some material is in the website -- brelvanto.wordpress.com

But looking for a template more consistent with the logo design, and more future looking.

Target Market(s)

Enterprise Clients

Industry/Entity Type

It Company

Font styles to use
Sans Serif

Colors
33a6d7
0255a3
0455a3
cfdeed
85abd2
3176b5

Requirements
Must have
• about, contact information, partner page, success stories, customer testimonials. links to social presence.
• pricing information

```html
<!DOCTYPE html>
<html lang="en">
<head>
<meta charset="utf-8">
<title>Brelvanto – Home</title>
<link rel="stylesheet" href="https://fonts.googleapis.com/css2?family=Questrial&family=Jost:wght@600&family=Arimo&display=swap">
<style>
  :root {
    --header-bg: #1f252e;
    --header-panel: #0d1014;
    --brand-blue: #33a6d7;
    --brand-grey: #6e6e6e;
    --nav-bg: #0d1014;
    --sky: #9cc1e4;
    --sky-deep: #85abd2;
    --panel: #cfdeed;
    --panel-light: #dde9f4;
    --ink: #111111;
    --footer-bg: #10151d;
    --icon-light: #e8eef4;
  }
  * { margin: 0; padding: 0; box-sizing: border-box; }
  html, body { width: 1200px; height: 1070px; overflow: hidden; }
  body { position: relative; background: var(--sky); font-family: "Questrial", sans-serif; color: var(--ink); }

  .site-header { position: absolute; left: 0; top: 0; width: 1200px; height: 318px; background: var(--header-bg); }
  .site-header svg { position: absolute; inset: 0; }
  .brand-mark { position: absolute; left: 330px; top: 115px; width: 110px; height: 110px; border-radius: 50%; background: var(--brand-blue); }
  .brand-name { position: absolute; left: 530px; top: 95px; font-family: "Questrial", sans-serif; font-size: 128px; line-height: 1; color: var(--brand-grey); letter-spacing: 2px; }

  .main-nav { position: absolute; left: 0; top: 318px; width: 1200px; height: 50px; }
  .nav-item { position: absolute; top: 8px; height: 37px; background: var(--nav-bg); color: var(--brand-blue);
    font-family: "Jost", sans-serif; font-weight: 600; font-size: 25px; letter-spacing: 1.5px;
    display: flex; align-items: center; justify-content: center; text-decoration: none; }
  .nav-home { left: 21px; width: 152px; clip-path: polygon(0 0, 100% 0, 97% 100%, 3% 100%); }
  .nav-platform { left: 176px; width: 198px; clip-path: polygon(2% 0, 97% 0, 100% 100%, 0 100%); }
  .nav-partners { left: 368px; width: 205px; clip-path: polygon(0 0, 100% 0, 100% 100%, 4% 100%); }
  .nav-blog { left: 578px; width: 192px; }
  .nav-about { left: 782px; width: 193px; }
  .nav-contact { left: 988px; width: 192px; }

  .hero-backdrop { position: absolute; left: 0; top: 364px; width: 1200px; height: 591px;
    background: radial-gradient(circle at 900px 380px, var(--sky-deep) 0 220px, transparent 221px),
                radial-gradient(circle at 1130px 620px, #8fb8df 0 200px, transparent 201px); opacity: .45; }
  .content-shapes { position: absolute; left: 0; top: 0; }

  .content { position: absolute; left: 37px; top: 472px; width: 690px; }
  .page-title { font-size: 96px; font-weight: 400; line-height: 1; letter-spacing: 1px; }
  .intro { margin-top: 12px; font-size: 20.5px; line-height: 22.4px; }
  .intro + .intro { margin-top: 44px; }

  .site-footer { position: absolute; left: 0; top: 955px; width: 1200px; height: 115px; background: var(--footer-bg); }
  .social-links { position: absolute; left: 48px; top: 32px; display: flex; gap: 26px; list-style: none; }
  .social-links a { display: flex; align-items: center; gap: 8px; color: var(--icon-light); text-decoration: none; font-size: 15px; }
  .social-square { width: 32px; height: 32px; border-radius: 4px; background: var(--brand-blue); }
  .site-address { position: absolute; right: 22px; top: 80px; font-family: "Arimo", sans-serif; font-size: 16px; color: var(--brand-blue); text-decoration: none; }
</style>
</head>
<body>
  <header class="site-header">
    <svg width="1200" height="318" viewBox="0 0 1200 318" aria-hidden="true">
      <polygon points="0,0 165,0 510,113 512,262 0,305" fill="var(--header-panel)"/>
      <polygon points="512,113 1200,0 1200,255 512,257" fill="var(--header-panel)"/>
    </svg>
    <span class="brand-mark" aria-hidden="true"></span>
    <span class="brand-name">Brelvanto</span>
  </header>

  <nav class="main-nav">
    <a class="nav-item nav-home" href="#">HOME</a>
    <a class="nav-item nav-platform" href="#">PLATFORM</a>
    <a class="nav-item nav-partners" href="#">PARTNERS</a>
    <a class="nav-item nav-blog" href="#">BLOG</a>
    <a class="nav-item nav-about" href="#">ABOUT</a>
    <a class="nav-item nav-contact" href="#">CONTACT</a>
  </nav>

  <div class="hero-backdrop" aria-hidden="true"></div>
  <svg class="content-shapes" width="1200" height="955" viewBox="0 0 1200 955" aria-hidden="true">
    <polygon points="0,389 813,430 813,880 0,910" fill="var(--panel)" opacity=".85"/>
    <polygon points="0,552 774,552 774,748 0,816" fill="var(--panel-light)" opacity=".8"/>
  </svg>

  <main class="content">
    <h1 class="page-title">HOME</h1>
    <p class="intro">Brelvanto is company which provides specialized offerings in IoT domain. Based in the heart of the Silicon Valley, California. Brelvanto is built on decades of experience and knowledge</p>
    <p class="intro">Brelvanto BX IoT platform for OEM’s is designed to ease the transition of Product companies from selling unconnected products, into providing service for connected devices.</p>
  </main>

  <footer class="site-footer">
    <ul class="social-links">
      <li><a href="#"><span class="social-square"></span>Linkwell</a></li>
      <li><a href="#"><span class="social-square"></span>Circlebook</a></li>
      <li><a href="#"><span class="social-square"></span>Chirpline</a></li>
    </ul>
    <a class="site-address" href="#">PRESSHARBOR.COM.</a>
  </footer>
</body>
</html>
```